Website Design for a holiday home letting busines

We require a redesign of our present website www.pinebrookstays.com. We want the website to stand out and look professional and clean to make holiday hunters want to book a caravan or lodge holiday with us. Our logo is red however we DO NOT want the website to be red. We want a natural colour scheme.

The final design should communicate that we are a professional company to book with.

On the home page we require;
Overview of company
Photo
Search box for holiday (check in)
Late Deals
Reviews
News

We would like the following pages designed; home page, available dates page, caravans page, content page.

The website should be responsive for smart phones. One website I do like is http://www.verdoliso.be/nl/

Target Market(s)

Families

Industry/Entity Type

Travel

Number of Pages Required

5+ page

Font styles to use
Serif

Requirements
Must have
• The project must be responsive for mobile phones and tablets.
• Ability to search for holiday home holidays
• We want a natural colour scheme.
Nice to have
• A style we like is http://www.verdoliso.be/nl/
Should not have
• Do not use red as a colour for the website. Our logo is red so this is the only time we want this used.

```html
<!DOCTYPE html>
<html lang="en">
<head>
<meta charset="utf-8">
<title>Pinebrook Stays – Private Holiday Rentals</title>
<link rel="stylesheet" href="https://fonts.googleapis.com/css2?family=Lato:wght@300;400;700&family=Open+Sans:wght@400;600&display=swap">
<style>
:root{
  --blue:#1c9be0;
  --blue-dark:#1580bd;
  --blue-deep:#0f6ea6;
  --ink:#3a3f45;
  --muted:#7b8188;
  --line:#dfe3e7;
  --paper:#ffffff;
  --mist:#f3f5f7;
  --night:#2b2f33;
  --star:#b5b9bd;
  --brand:#c8242b;
}
*{box-sizing:border-box;margin:0;padding:0}
html,body{width:1200px;height:3000px;overflow:hidden}
body{font-family:"Open Sans",Arial,sans-serif;color:var(--ink);background:var(--paper);font-size:11px;line-height:1.55}
.wrap{width:960px;margin:0 auto;position:relative}
h1,h2,h3,h4{font-family:"Lato",Arial,sans-serif;font-weight:400}
.btn{display:inline-block;background:var(--blue);color:#fff;font-size:11px;padding:7px 18px;border-radius:2px;text-decoration:none;font-family:"Lato",sans-serif}

/* header */
.site-header{height:56px}
.site-header .wrap{display:flex;justify-content:space-between;align-items:center;height:56px}
.brand{display:flex;align-items:center;gap:10px}
.brand-mark{width:26px;height:26px;border-radius:50%;background:var(--brand)}
.brand-name{font-family:"Lato",sans-serif;font-weight:700;font-size:20px;color:var(--night);line-height:1}
.brand-sub{font-size:9px;color:var(--muted);display:block;margin-top:3px}
.contact-line{display:flex;gap:22px;font-size:11px;color:var(--muted);align-items:center}
.contact-line span{display:flex;align-items:center;gap:5px}

.main-nav{height:26px;background:var(--mist);border-top:1px solid var(--line);border-bottom:1px solid var(--line)}
.main-nav ul{list-style:none;display:flex;height:24px}
.main-nav li{font-size:10.5px;padding:0 14px;line-height:24px;color:var(--muted)}
.main-nav li.is-active{background:var(--blue);color:#fff}

/* hero */
.hero{height:478px;position:relative;background:linear-gradient(160deg,#9fc3dc 0%,#c9d9e4 35%,#e9e3d6 60%,#7fa8c6 100%);overflow:hidden}
.hero-copy{position:absolute;top:150px;left:0;right:0;text-align:center;color:#fff}
.hero-copy h1{font-size:46px;font-weight:300;letter-spacing:.5px}
.hero-copy p{font-size:17px;margin:8px auto 22px;width:360px;font-family:"Lato",sans-serif;line-height:1.3}
.booking{position:absolute;right:120px;top:318px;width:190px;background:rgba(28,155,224,.92);color:#fff;padding:14px 14px 12px;text-align:center}
.booking h3{font-size:14px;line-height:1.25;margin-bottom:10px}
.booking .fields{display:flex;gap:8px}
.booking label{flex:1;font-size:9px;text-align:left}
.booking .field{display:block;margin-top:3px;height:20px;background:#fff;border-radius:2px}

/* section titles */
.section-title{text-align:center;color:var(--blue);font-size:27px;margin-bottom:18px}
.boxed-title{display:inline-block;border:1px solid var(--line);padding:4px 26px}

.overview{height:242px;padding-top:34px;text-align:center}
.overview p{width:640px;margin:0 auto 16px;font-size:10.5px;color:var(--muted)}

.no-deposit{height:360px;background:linear-gradient(180deg,#3b3a38,#5a564f 55%,#2f2e2c);position:relative;padding-top:20px;text-align:center}
.no-deposit h2{color:#fff;font-size:30px;font-weight:300;margin-bottom:16px}
.tour-media{width:580px;height:266px;margin:0 auto;background:linear-gradient(135deg,#e9e2d5,#c9b79c 50%,#8f7f6a);position:relative}
.play{position:absolute;left:50%;top:50%;transform:translate(-50%,-50%)}

/* cards */
.fleet{height:400px;padding-top:30px}
.row-title{display:flex;align-items:center;gap:16px;margin-bottom:16px}
.row-title::before,.row-title::after{content:"";flex:1;height:1px;background:var(--line)}
.row-title h2{color:var(--blue);font-size:25px}
.pager{display:flex;gap:3px}
.pager i{width:14px;height:14px;background:var(--blue);display:block}
.cards{display:flex;gap:30px}
.card{width:300px}
.card h4{font-size:12px;margin-bottom:6px;color:var(--ink)}
.card-media{height:190px;position:relative}
.tone-a{background:linear-gradient(135deg,#5b5046,#2e2925)}
.tone-b{background:linear-gradient(135deg,#e7dcc8,#b89e7c 60%,#7f6a53)}
.tone-c{background:linear-gradient(135deg,#f0ece4,#cfc4b2 55%,#9ca37e)}
.specs{position:absolute;left:20px;top:20px;width:160px;color:#eee;font-size:10px;background:rgba(0,0,0,.45);padding:8px 10px}
.specs div{display:flex;justify-content:space-between;border-bottom:1px solid rgba(255,255,255,.15);padding:2px 0}
.card-meta{display:flex;justify-content:space-between;align-items:center;padding:8px 0;font-size:10.5px}
.stars{color:var(--star);letter-spacing:1px;font-size:11px}
.card .btn{display:block;width:110px;margin:0 auto;text-align:center;padding:5px 0}

.late-deals{height:430px;background:linear-gradient(180deg,#3d3f42,#55524c 50%,#343537);padding-top:22px;color:#fff}
.late-deals .section-title{color:#fff;font-size:28px;margin-bottom:10px}
.late-deals .pager{position:absolute;right:0;top:2px}
.late-deals .card h4{color:#fff;margin-bottom:0}
.late-deals .date{font-size:10px;color:#d5d8db;margin-bottom:6px}
.late-deals .card-media{border:4px solid #fff;height:200px}

.blog{height:310px;padding-top:26px}
.blog .pager{position:absolute;right:0;top:6px}
.posts{display:flex;gap:30px}
.post{width:300px}
.post h3{color:var(--blue);font-size:13px;font-weight:700;line-height:1.3}
.post .date{font-size:9.5px;color:var(--muted);margin:4px 0 6px}
.post p{font-size:10px;color:var(--muted);margin-bottom:10px}
.post .btn{padding:5px 14px;font-size:10px}

.review{height:190px;background:linear-gradient(90deg,#3a3c3f,#5c5a55 50%,#3a3c3f);text-align:center;color:#fff;padding-top:18px}
.avatar{width:62px;height:62px;border-radius:50%;background:linear-gradient(135deg,#d9cbb8,#a48d72);border:3px solid #fff;margin:0 auto 6px}
.review h2{font-size:24px;font-weight:300;margin-bottom:6px}
.review p{width:600px;margin:0 auto;font-size:10px;color:#e3e5e7}

.get-in-touch{height:310px;padding-top:28px;text-align:center}
.get-in-touch .section-title{color:var(--ink);margin-bottom:2px}
.get-in-touch .sub{color:var(--blue);font-size:15px;font-family:"Lato",sans-serif;margin-bottom:18px}
.form{width:520px;margin:0 auto;display:flex;gap:20px;text-align:left}
.form .col{flex:1}
.form label{display:block;font-size:10px;color:var(--muted)}
.form .input{display:block;height:22px;border:1px solid var(--line);margin:2px 0 8px}
.form .textarea{height:112px}
.get-in-touch .btn{margin-top:10px;padding:6px 26px}

.site-footer{height:180px;background:var(--blue);color:#fff;padding-top:24px}
.footer-cols{display:flex;gap:30px}
.footer-cols>div{flex:1;font-size:10px}
.footer-cols h4{font-size:14px;margin-bottom:8px}
.site-footer .brand-name{color:#fff;font-size:17px}
.site-footer .brand-mark{background:#fff}
.feed li{list-style:none;display:flex;gap:6px;align-items:center;margin-bottom:6px}
.feed li::before{content:"";width:16px;height:16px;background:rgba(255,255,255,.35);flex:none}
.socials{display:flex;gap:6px;margin-top:10px}
.socials i{width:22px;height:22px;border-radius:50%;background:rgba(255,255,255,.35);display:block}
.subscribe{display:flex;margin-top:10px}
.subscribe span{flex:1;height:24px;background:#fff;color:var(--muted);padding:5px 8px}
.subscribe b{background:var(--night);padding:5px 12px;font-weight:400}
.bottom-bar{height:40px;background:var(--blue-deep);color:#d7ecf8;font-size:9.5px}
.bottom-bar .wrap{display:flex;justify-content:space-between;align-items:center;height:40px}
.bottom-bar nav{display:flex;gap:14px}
</style>
</head>
<body>

<header class="site-header">
  <div class="wrap">
    <div class="brand">
      <span class="brand-mark"></span>
      <div><span class="brand-name">Pinebrook Stays</span><span class="brand-sub">at Alderwood Holiday Park</span></div>
    </div>
    <div class="contact-line">
      <span><svg width="12" height="12" viewBox="0 0 24 24"><path fill="#1c9be0" d="M6.6 10.8a15 15 0 0 0 6.6 6.6l2.2-2.2a1 1 0 0 1 1-.25 11 11 0 0 0 3.6.6 1 1 0 0 1 1 1V20a1 1 0 0 1-1 1A17 17 0 0 1 3 4a1 1 0 0 1 1-1h3.5a1 1 0 0 1 1 1c0 1.25.2 2.45.6 3.6a1 1 0 0 1-.25 1z"/></svg>01632 960 418</span>
      <span><svg width="12" height="12" viewBox="0 0 24 24"><rect x="2" y="5" width="20" height="14" fill="none" stroke="#1c9be0" stroke-width="2"/><path d="M2 6l10 7 10-7" fill="none" stroke="#1c9be0" stroke-width="2"/></svg>info@pinebrookstays.com</span>
    </div>
  </div>
</header>

<nav class="main-nav">
  <ul class="wrap">
    <li class="is-active">Home</li><li>News</li><li>Reviews</li><li>Caravans &amp; Lodges</li><li>2015 Holidays</li><li>2016 Holidays</li><li>Alderwood Park</li><li>Local Attractions</li><li>Contact</li>
  </ul>
</nav>

<section class="hero" role="img" aria-label="Photo of a smiling family enjoying a holiday by the sea">
  <div class="hero-copy">
    <h1>Private Holiday Rentals</h1>
    <p>Quality Lodge &amp; Caravan Hire at Alderwood Holiday Park</p>
    <a class="btn">More Details</a>
  </div>
  <form class="booking">
    <h3>Book Here your holidays in minutes</h3>
    <div class="fields">
      <label>Check in<span class="field"></span></label>
      <label>Check out<span class="field"></span></label>
    </div>
  </form>
</section>

<section class="overview">
  <h2 class="section-title"><span class="boxed-title">Overview of company</span></h2>
  <p>Would you like to book a 2015 caravan or lodge holiday at Alderwood Holiday Park? We have flexible stays for families. We have flexible low cost weekly and monthly payment plans available from as little as £10 per week by direct debit. This means you can secure your holiday now and pay nothing more until the balance is due.</p>
  <a class="btn">Read More</a>
</section>

<section class="no-deposit">
  <h2>No deposit holidays</h2>
  <div class="tour-media" role="img" aria-label="Video still of a bright caravan kitchen and lounge">
    <svg class="play" width="54" height="54" viewBox="0 0 54 54"><circle cx="27" cy="27" r="27" fill="#e8702a"/><path d="M21 16l18 11-18 11z" fill="#fff"/></svg>
  </div>
</section>

<section class="fleet">
  <div class="wrap">
    <div class="row-title"><h2>Our caravans and lodges</h2><div class="pager"><i></i><i></i></div></div>
    <div class="cards">
      <article class="card">
        <h4>The Ashford</h4>
        <div class="card-media tone-a" role="img" aria-label="Photo of a lodge interior">
          <div class="specs"><div><span>Caravan type</span><span>Lodge</span></div><div><span>Sleeps</span><span>6</span></div><div><span>Berths</span><span>6</span></div><div><span>Bedrooms</span><span>3</span></div></div>
        </div>
        <div class="card-meta"><span>Lodge</span><span class="stars">★★★★★</span></div>
        <a class="btn">More Details</a>
      </article>
      <article class="card">
        <h4>The Kestrel</h4>
        <div class="card-media tone-b" role="img" aria-label="Photo of a caravan lounge"></div>
        <div class="card-meta"><span>Caravan</span><span class="stars">★★★★★</span></div>
        <a class="btn">More Details</a>
      </article>
      <article class="card">
        <h4>The Hawthorn</h4>
        <div class="card-media tone-c" role="img" aria-label="Photo of a caravan dining area"></div>
        <div class="card-meta"><span>Caravan</span><span class="stars">★★★★★</span></div>
        <a class="btn">More Details</a>
      </article>
    </div>
  </div>
</section>

<section class="late-deals">
  <div class="wrap">
    <h2 class="section-title">Late Deals</h2>
    <div class="pager"><i></i><i></i></div>
    <div class="cards">
      <article class="card">
        <h4>The Linden</h4><div class="date">Friday 04 September 2015 (3 nights)</div>
        <div class="card-media tone-a" role="img" aria-label="Photo of a caravan living room"></div>
        <div class="card-meta"><span>Caravan</span><span class="stars">★★★★★</span></div>
        <a class="btn">Book Now</a>
      </article>
      <article class="card">
        <h4>The Kestrel</h4><div class="date">Friday 04 September 2015 (3 nights)</div>
        <div class="card-media tone-b" role="img" aria-label="Photo of a caravan kitchen"></div>
        <div class="card-meta"><span>Caravan</span><span class="stars">★★★★★</span></div>
        <a class="btn">Book Now</a>
      </article>
      <article class="card">
        <h4>The Hawthorn</h4><div class="date">Friday 04 September 2015 (3 nights)</div>
        <div class="card-media tone-c" role="img" aria-label="Photo of a caravan lounge"></div>
        <div class="card-meta"><span>Caravan</span><span class="stars">★★★★★</span></div>
        <a class="btn">Book Now</a>
      </article>
    </div>
  </div>
</section>

<section class="blog">
  <div class="wrap">
    <h2 class="section-title">Latest Blog</h2>
    <div class="pager"><i></i><i></i></div>
    <div class="posts">
      <article class="post">
        <h3>Summer evenings by the lake, family fun and walks along the coast</h3>
        <div class="date">Posted 12 August 2015</div>
        <p>Long light evenings make the park perfect for families. Children enjoy the play areas while parents relax on the deck. Nearby beaches and woodland paths offer easy walks for all ages and plenty of fresh air.</p>
        <a class="btn">Read More</a>
      </article>
      <article class="post">
        <h3>New lodges arriving this season with spacious decks and views</h3>
        <div class="date">Posted 28 July 2015</div>
        <p>We are pleased to welcome new lodges to our range this year. Each one offers open plan living, modern kitchens and a private deck, giving families more space and comfort during their stay with us.</p>
        <a class="btn">Read More</a>
      </article>
      <article class="post">
        <h3>Local days out, castles, markets and quiet beaches nearby</h3>
        <div class="date">Posted 15 July 2015</div>
        <p>There is so much to explore just a short drive away. Visit historic towns, browse local markets and find quiet sandy beaches. Our guide lists favourite spots chosen by guests who return year after year.</p>
        <a class="btn">Read More</a>
      </article>
    </div>
  </div>
</section>

<section class="review">
  <div class="avatar" role="img" aria-label="Guest portrait"></div>
  <h2>Latest Review</h2>
  <p>Had a lovely stay with the family. The caravan was spotless and had everything we needed. Booking was simple and the team were friendly and helpful throughout. We will certainly be booking again next year.</p>
</section>

<section class="get-in-touch">
  <h2 class="section-title">Get In Touch</h2>
  <div class="sub">Questions? Comments? Suggestions?</div>
  <form class="form">
    <div class="col">
      <label>Your Name*<span class="input"></span></label>
      <label>Your Phone*<span class="input"></span></label>
      <label>Your Email*<span class="input"></span></label>
    </div>
    <div class="col">
      <label>Message<span class="input textarea"></span></label>
    </div>
  </form>
  <a class="btn">Submit</a>
</section>

<footer class="site-footer">
  <div class="wrap footer-cols">
    <div>
      <div class="brand"><span class="brand-mark"></span><span class="brand-name">Pinebrook Stays</span></div>
      <p style="margin-top:10px">Quality caravan and lodge holidays for families at Alderwood Holiday Park.</p>
    </div>
    <div>
      <h4>Community Feed</h4>
      <ul class="feed"><li>Late deals now available for September</li><li>Thank you to all our summer guests</li><li>New lodges arriving this season</li></ul>
    </div>
    <div>
      <h4>Get Social with us</h4>
      <p>Follow us for news, offers and holiday ideas from the park and share your photos with us.</p>
      <div class="socials"><i></i><i></i><i></i><i></i></div>
    </div>
    <div>
      <h4>Share your thoughts!</h4>
      <p>Sign up to hear about new deals, open dates and park news before anyone else.</p>
      <div class="subscribe"><span>Email Address</span><b>Send</b></div>
    </div>
  </div>
</footer>

<div class="bottom-bar">
  <div class="wrap">
    <nav><span>Home</span><span>News</span><span>Reviews</span><span>Caravans &amp; Lodges</span><span>2015 Holidays</span><span>2016 Holidays</span><span>Alderwood Park</span><span>Local Attractions</span><span>Contact</span></nav>
    <span>Copyright © 2015 Pinebrook Stays</span>
  </div>
</div>

</body>
</html>
```